Brightfen Business Card Redesign & Logo Update

We need to update our business cards to something more modern and fresh. Brightfen can provide the current color schemes and old design examples, but welcome creativity in helping us with this redesign. PLEASE NOTE that we no longer utilize the "tree" and/or "leaf" imagery in our branding. If able would apprecaite an update on the quality of our "words only" logo in Ai. / PNG formats too.

Target Market(s)

Investors, landowners, corporate partners, contractors

Industry/Entity Type

Environmental Restoration & Conservation

Contact Information for Business Card

Logo, persons name, title, mailing address, phone and email, website url

Font styles to use
Other font styles liked:
• Merriweather

Requirements
Nice to have
• Logo, persons name, title, mailing address, phone and email, website url, but open to ideams
Should not have
• No all back backgrounds

```html
<!DOCTYPE html>
<html lang="en">
<head>
<meta charset="UTF-8">
<title>Brightfen Business Card</title>
<link href="https://fonts.googleapis.com/css2?family=Montserrat:wght@400;500;800&display=swap" rel="stylesheet">
<style>
  :root {
    --green: #147a36;
    --green-dark: #11702f;
    --orange: #e57700;
    --ink: #2a2a2a;
    --paper: #ffffff;
    --backdrop: #dcdcdc;
    --rule: #8a8a8a;
  }
  * { box-sizing: border-box; margin: 0; padding: 0; }
  html, body {
    width: 1200px; height: 1200px; overflow: hidden;
    background: var(--backdrop);
    font-family: "Montserrat", sans-serif;
  }
  .sheet {
    width: 1200px; height: 1200px;
    display: flex; flex-direction: column; align-items: center; justify-content: center;
    gap: 44px;
  }
  .card {
    position: relative;
    width: 900px; height: 514px;
    border-radius: 34px;
    overflow: hidden;
  }
  /* Front */
  .card--front { background: var(--paper); }
  .brand {
    position: absolute; left: 120px; top: 100px;
    display: flex; align-items: center; gap: 18px;
  }
  .brand__mark { width: 30px; height: 30px; background: var(--green); }
  .brand__name {
    font-weight: 800; font-size: 76px; letter-spacing: 2px;
    text-transform: uppercase; color: var(--green); line-height: 1;
  }
  .person {
    position: absolute; left: 76px; top: 318px;
    border-left: 6px solid var(--orange);
    padding-left: 18px;
  }
  .person__name {
    font-weight: 500; font-size: 40px; color: var(--orange);
    text-transform: uppercase; line-height: 1.05; letter-spacing: 0.5px;
  }
  .person__title {
    font-weight: 400; font-size: 18px; color: var(--ink);
    text-transform: uppercase; margin-top: 4px;
  }
  .divider {
    position: absolute; left: 468px; top: 250px;
    width: 1px; height: 120px; background: var(--rule);
  }
  .contact {
    position: absolute; left: 520px; top: 226px;
    list-style: none;
    font-size: 19px; color: var(--ink); line-height: 1.25;
  }
  .contact__item { display: flex; align-items: flex-start; gap: 10px; margin-bottom: 4px; }
  .contact__icon { width: 20px; height: 20px; flex: none; margin-top: 2px; fill: var(--orange); }
  .band { position: absolute; bottom: 0; }
  .band--orange { left: 0; width: 56%; height: 40px; background: var(--orange); }
  .band--green  { right: 0; width: 42.5%; height: 64px; background: var(--green); }
  /* Back */
  .card--back {
    background: linear-gradient(100deg, var(--green-dark) 0%, var(--green) 45%, #2a8c4c 55%, var(--green) 70%);
    display: flex; align-items: center; justify-content: center;
  }
  .card--back .brand { position: static; }
  .card--back .brand__mark { width: 40px; height: 40px; background: var(--orange); }
  .card--back .brand__name { color: var(--paper); font-size: 104px; }
</style>
</head>
<body>
<main class="sheet">
  <section class="card card--front" aria-label="Business card front">
    <div class="brand">
      <span class="brand__mark"></span>
      <span class="brand__name">Brightfen</span>
    </div>

    <div class="person">
      <p class="person__name">John Doe</p>
      <p class="person__title">Position</p>
    </div>

    <span class="divider"></span>

    <ul class="contact">
      <li class="contact__item">
        <svg class="contact__icon" viewBox="0 0 24 24"><path d="M6.6 10.8a15 15 0 0 0 6.6 6.6l2.2-2.2c.3-.3.7-.4 1-.2 1.1.4 2.3.6 3.6.6.6 0 1 .4 1 1V20c0 .6-.4 1-1 1C10.6 21 3 13.4 3 4c0-.6.4-1 1-1h3.5c.6 0 1 .4 1 1 0 1.3.2 2.5.6 3.6.1.3 0 .7-.2 1z"/></svg>
        <span>(000) 000 0000</span>
      </li>
      <li class="contact__item">
        <svg class="contact__icon" viewBox="0 0 24 24"><path d="M2 5h20v14H2z M2 5l10 8 10-8" fill="none" stroke="#e57700" stroke-width="2"/></svg>
        <span>email@youremail.com</span>
      </li>
      <li class="contact__item">
        <svg class="contact__icon" viewBox="0 0 24 24" fill="none" stroke="#e57700" stroke-width="1.8"><circle cx="12" cy="12" r="9.5"/><ellipse cx="12" cy="12" rx="4" ry="9.5"/><path d="M2.5 12h19M4 7h16M4 17h16"/></svg>
        <span>www.yourwebsite.com</span>
      </li>
      <li class="contact__item">
        <svg class="contact__icon" viewBox="0 0 24 24"><path d="M12 2a7 7 0 0 0-7 7c0 5 7 13 7 13s7-8 7-13a7 7 0 0 0-7-7zm0 9.5A2.5 2.5 0 1 1 12 6.5a2.5 2.5 0 0 1 0 5z"/></svg>
        <span>123 Name Street, 000<br>Your City, 00000-000</span>
      </li>
    </ul>

    <span class="band band--orange"></span>
    <span class="band band--green"></span>
  </section>

  <section class="card card--back" aria-label="Business card back">
    <div class="brand">
      <span class="brand__mark"></span>
      <span class="brand__name">Brightfen</span>
    </div>
  </section>
</main>
</body>
</html>
```